Vantro cards

I am in the auto motive, transportation business I would like a business card that is Something cool, modern edgy, having to do with car culture. I offer towing service for high and exotic cars. I also provide towing for collisions and car accidents. I offer open and enclosed transport nationwide.

Target Market(s)

Car culture people high end auto collectors

Industry/Entity Type

Towing car carrier

Contact Information for Business Card

My company colors black yellow and silver

Font styles to use
Serif

```html
<!DOCTYPE html>
<html lang="en">
<head>
<meta charset="utf-8">
<title>Vantro Business Cards</title>
<link rel="stylesheet" href="https://fonts.googleapis.com/css2?family=Arimo:wght@400;700&display=swap">
<style>
  :root {
    --bg: #2a2a2a;
    --card: #1c1c1d;
    --card-deep: #111112;
    --yellow: #f6df4b;
    --silver: #c9c9c9;
    --white: #f2f2f2;
  }
  * { box-sizing: border-box; margin: 0; padding: 0; }
  html, body { width: 1200px; height: 900px; overflow: hidden; }
  body {
    background: var(--bg);
    font-family: "Arimo", Arial, sans-serif;
    display: flex;
    flex-direction: column;
    align-items: center;
    justify-content: center;
    gap: 44px;
  }
  .card {
    position: relative;
    width: 660px;
    height: 377px;
    background: var(--card);
    border: 3px solid var(--yellow);
    overflow: hidden;
  }
  /* front */
  .card-front .pattern {
    position: absolute;
    inset: 0;
    background: linear-gradient(135deg, #151516 0%, #1f1f21 50%, #0e0e0f 100%);
  }
  .card-front .brand {
    position: absolute;
    top: 50%;
    left: 50%;
    transform: translate(-50%, -50%);
    display: flex;
    align-items: center;
    gap: 14px;
    padding: 18px 30px;
    background: var(--card);
  }
  .brand-mark {
    width: 18px;
    height: 18px;
    background: var(--yellow);
  }
  .brand-name {
    font-weight: 700;
    font-size: 58px;
    letter-spacing: 4px;
    color: var(--silver);
    text-transform: uppercase;
  }
  /* back */
  .card-back .brand {
    position: absolute;
    top: 48px;
    right: 44px;
    display: flex;
    align-items: center;
    gap: 12px;
  }
  .card-back .brand-name { font-size: 46px; letter-spacing: 3px; }
  .card-back .brand-mark { width: 14px; height: 14px; }
  .rule-long {
    position: absolute;
    left: 40px;
    right: 36px;
    top: 178px;
    height: 1px;
    background: var(--yellow);
  }
  .holder {
    position: absolute;
    left: 40px;
    top: 140px;
  }
  .holder-name {
    font-weight: 700;
    font-size: 25px;
    letter-spacing: 1px;
    color: var(--yellow);
    text-transform: uppercase;
  }
  .holder-role {
    margin-top: 14px;
    font-size: 17px;
    color: var(--white);
  }
  .rule-short {
    position: absolute;
    left: 40px;
    top: 222px;
    width: 200px;
    height: 1px;
    background: var(--yellow);
  }
  .contact-list {
    position: absolute;
    left: 40px;
    top: 236px;
    list-style: none;
  }
  .contact-list li {
    display: flex;
    align-items: center;
    gap: 12px;
    height: 27px;
    font-size: 17px;
    color: var(--white);
  }
  .contact-list svg { width: 16px; height: 16px; flex: none; }
  .address {
    position: absolute;
    right: 40px;
    top: 196px;
    text-align: right;
    font-size: 16px;
    line-height: 1.45;
    color: var(--white);
  }
</style>
</head>
<body>

  <section class="card card-front">
    <div class="pattern" role="img" aria-label="Repeating tone-on-tone brand emblem pattern in dark grey"></div>
    <div class="brand">
      <span class="brand-mark"></span>
      <span class="brand-name">Vantro</span>
    </div>
  </section>

  <section class="card card-back">
    <div class="brand">
      <span class="brand-mark"></span>
      <span class="brand-name">Vantro</span>
    </div>

    <div class="rule-long"></div>

    <div class="holder">
      <h1 class="holder-name">Dorian Kell</h1>
      <p class="holder-role">CEO/Founder</p>
    </div>

    <div class="rule-short"></div>

    <ul class="contact-list">
      <li>
        <svg viewBox="0 0 16 16" aria-hidden="true"><path fill="#f6df4b" d="M3.5 1.5l2.2 2.6-1.2 1.6c.9 2 2.3 3.5 4.3 4.4l1.6-1.2 2.6 2.2-1.3 2.4C6.6 13 2.9 9.3 1.2 4.3z"/></svg>
        (555) 318 4402
      </li>
      <li>
        <svg viewBox="0 0 16 16" aria-hidden="true"><rect x="4" y="1" width="8" height="14" rx="1.5" fill="none" stroke="#f6df4b" stroke-width="1.6"/><circle cx="8" cy="12.3" r="0.9" fill="#f6df4b"/></svg>
        (555) 762 9015
      </li>
      <li>
        <svg viewBox="0 0 16 16" aria-hidden="true"><rect x="1" y="3" width="14" height="10" fill="#f6df4b"/><path d="M1 3.5l7 5 7-5" fill="none" stroke="#1c1c1d" stroke-width="1.3"/></svg>
        info@vantrotransport.com
      </li>
      <li>
        <svg viewBox="0 0 16 16" aria-hidden="true"><g fill="none" stroke="#f6df4b" stroke-width="1.3"><circle cx="8" cy="8" r="6.5"/><ellipse cx="8" cy="8" rx="3" ry="6.5"/><path d="M1.5 8h13M2.5 4.8h11M2.5 11.2h11"/></g></svg>
        www.vantrotransport.com
      </li>
    </ul>

    <address class="address" style="font-style:normal">
      P.O. Box 7730 Harlow Road<br>
      Region Field CD 4417
    </address>
  </section>

</body>
</html>
```